Bramblewood Card Company Business Cards

We are a trading card store with Glimmorax, sports and other TCG cards, we need a business card design that encompasses a clean cut, modern style with a retro flare. website is bramblewoodcardco.com for reference. Can utilize a comic book era feel or a more modern outdoor feel to utilize the "Pacific Northwest" elements of tress, mountains, etc.

Industry/Entity Type

Trading cards and collectibles

Contact Information for Business Card

business name, email address, phone number, name, owner job title

Font styles to use
Sans Serif

```html
<!DOCTYPE html>
<html lang="en">
<head>
<meta charset="utf-8">
<title>Bramblewood Card Company – Business Cards</title>
<link href="https://fonts.googleapis.com/css2?family=Montserrat:wght@400;500;700;800&display=swap" rel="stylesheet">
<style>
  :root {
    --backdrop: #c4c4c4;
    --card-grey: #737373;
    --card-white: #ffffff;
    --accent-blue: #22bde0;
    --text-light: #f2f2f2;
  }
  * { margin: 0; padding: 0; box-sizing: border-box; }
  html, body { width: 1200px; height: 815px; overflow: hidden; }
  body {
    background: var(--backdrop);
    font-family: "Montserrat", Arial, sans-serif;
    display: flex;
    align-items: center;
    justify-content: center;
    gap: 44px;
  }
  .card {
    position: relative;
    width: 520px;
    height: 297px;
    border-radius: 22px;
    overflow: hidden;
    box-shadow: 0 10px 24px rgba(0,0,0,0.25);
  }
  .card-front { background: var(--card-white); }
  .card-back { background: var(--card-grey); display: flex; align-items: center; justify-content: center; }
  .front-shapes { position: absolute; inset: 0; }

  .brand-mark {
    position: absolute;
    display: flex;
    align-items: center;
    gap: 10px;
    font-weight: 800;
    text-transform: uppercase;
    letter-spacing: 0.06em;
    line-height: 1.15;
  }
  .brand-mark .brand-dot { border-radius: 50%; flex: none; }
  .front-brand { top: 40px; left: 190px; color: var(--card-grey); font-size: 17px; }
  .front-brand .brand-dot { width: 30px; height: 30px; background: var(--card-grey); }
  .back-brand { position: static; color: var(--card-white); font-size: 30px; gap: 16px; }
  .back-brand .brand-dot { width: 54px; height: 54px; background: var(--card-white); }

  .person { position: absolute; left: 140px; top: 182px; color: var(--text-light); }
  .person-name { color: var(--accent-blue); font-weight: 700; font-size: 22px; line-height: 26px; letter-spacing: 0.05em; text-transform: uppercase; }
  .person-title { font-size: 12px; letter-spacing: 0.08em; text-transform: uppercase; margin-top: 1px; }
  .contact-list { list-style: none; margin-top: 10px; font-size: 11.5px; }
  .contact-list li { display: flex; align-items: center; gap: 7px; height: 16px; }
  .contact-list svg { width: 10px; height: 10px; fill: var(--accent-blue); flex: none; }

  .address {
    position: absolute;
    right: 26px;
    top: 232px;
    text-align: right;
    color: var(--text-light);
    font-size: 12px;
    line-height: 1.4;
  }
</style>
</head>
<body>
  <section class="card card-front">
    <svg class="front-shapes" viewBox="0 0 520 297" aria-hidden="true">
      <path d="M24 297 C26 196 78 168 228 142 C378 116 416 64 430 0" transform="translate(-12,-8)" fill="none" stroke="var(--accent-blue)" stroke-width="7"/>
      <path d="M36 297 C38 200 90 178 240 152 C390 126 428 70 442 0 L520 0 L520 297 Z" fill="var(--card-grey)"/>
    </svg>

    <div class="brand-mark front-brand">
      <span class="brand-dot"></span>
      <span>Bramblewood<br>Card Company</span>
    </div>

    <div class="person">
      <div class="person-name">Dana Hollis</div>
      <div class="person-title">Manager</div>
      <ul class="contact-list">
        <li><svg viewBox="0 0 10 10"><path d="M2 0.5 L3.8 2.8 L2.9 3.9 C3.6 5.3 4.7 6.4 6.1 7.1 L7.2 6.2 L9.5 8 L8.3 9.5 C4.2 9.2 0.8 5.8 0.5 1.7 Z"/></svg>(555) 014-2290</li>
        <li><svg viewBox="0 0 10 10"><path d="M0 2 H10 V8 H0 Z M0.6 2.4 L5 5.6 L9.4 2.4" stroke="var(--card-grey)" stroke-width="0.8"/></svg>hello@bramblewoodcardco.com</li>
        <li><svg viewBox="0 0 10 10"><circle cx="5" cy="5" r="4.6"/><path d="M0.4 5 H9.6 M5 0.4 C2.6 3 2.6 7 5 9.6 M5 0.4 C7.4 3 7.4 7 5 9.6" stroke="var(--card-grey)" stroke-width="0.7" fill="none"/></svg>www.bramblewoodcardco.com</li>
      </ul>
    </div>

    <div class="address">48 Cedar Ridge Lane<br>Evergreen, WA 98001</div>
  </section>

  <section class="card card-back">
    <div class="brand-mark back-brand">
      <span class="brand-dot"></span>
      <span>Bramblewood<br>Card Company</span>
    </div>
  </section>
</body>
</html>
```